Tovimar Community Development Planning New web site

Design a new web site. I have a budget of $1,500.00.
Attached on PowerPoint is a complete site plan. Home page and linked pages.
10 - 12 pages. All copy and photos will be supplied. (300dpi)
I have shown them the concept which they like.
No data bases required. Home page with animations dissolving.
They former web site has been taken down. They have been in business 30 years in New Jersey
Colors teal blues and greens
There will be a new logo)being designed)
The text in home page copy will give you a detailed story what they are all about.

files have been approved for Tovimar, Inc.   Brenton is the designer

```html
<!DOCTYPE html>
<html lang="en">
<head>
<meta charset="utf-8">
<title>Tovimar, Inc. — Community Development Planning</title>
<link href="https://fonts.googleapis.com/css2?family=Mulish:wght@400;600&family=Open+Sans:wght@400;600&display=swap" rel="stylesheet">
<style>
  :root{
    --green:#4b9f13;
    --yellow:#f1c100;
    --ink:#1b1b1b;
    --body:#2e2e2e;
    --muted:#7a7a7a;
    --rule:#d6d6d6;
    --white:#ffffff;
    --nav-divider:#5aaf20;
  }
  *{box-sizing:border-box;margin:0;padding:0}
  html,body{width:1042px;height:1200px;overflow:hidden;background:var(--white)}
  body{position:relative;font-family:"Open Sans",Arial,sans-serif;color:var(--body)}
  .abs{position:absolute}

  /* header */
  .site-header{left:0;top:0;width:1042px;height:45px;background:var(--green)}
  .brand{left:110px;top:10px;display:flex;align-items:center;gap:6px;color:var(--white);
    font-family:"Mulish",Arial,sans-serif;font-weight:600;font-size:19px;line-height:24px}
  .brand-square{width:11px;height:11px;background:var(--white)}
  .main-nav{right:108px;top:0;display:flex;height:45px}
  .main-nav a{display:block;padding:0 7px;line-height:45px;color:var(--white);text-decoration:none;
    font-family:"Mulish",Arial,sans-serif;font-size:12.4px;border-left:1px solid var(--nav-divider)}
  .main-nav a:first-child{border-left:none}
  .main-nav a.is-active{color:var(--yellow)}

  .dropdown{left:518px;top:45px;width:188px;height:101px;background:var(--white);
    box-shadow:0 1px 4px rgba(0,0,0,.3);padding:13px 11px 0 12px;z-index:3}
  .dropdown::before{content:"";position:absolute;left:14px;top:-6px;border:6px solid transparent;border-top:0;border-bottom-color:var(--white)}
  .dropdown a{display:block;font-family:"Open Sans",Arial,sans-serif;font-size:9px;color:var(--ink);
    text-decoration:none;line-height:20.5px;border-bottom:1px solid #e3e3e3}
  .dropdown a:last-child{border-bottom:none}

  /* hero */
  .hero{left:0;top:45px;width:1042px;height:463px;
    background:linear-gradient(135deg,#c9ccd0 0%,#8d8a86 35%,#4d4a48 60%,#b9b5ae 100%)}
  .hero-band{left:0;top:361px;width:1042px;height:147px;background:rgba(40,40,40,.62)}
  .hero-points{left:110px;top:391px;list-style:none}
  .hero-points li{position:relative;padding-left:13px;color:var(--white);font-family:"Mulish",Arial,sans-serif;
    font-size:12.3px;line-height:22.3px}
  .hero-points li::before{content:"";position:absolute;left:0;top:7px;width:8px;height:8px;border-radius:50%;background:var(--yellow)}
  .cta{left:762px;top:434px;width:171px;height:39px;background:var(--yellow);color:#3a3000;
    font-family:"Mulish",Arial,sans-serif;font-size:13.2px;line-height:39px;text-align:center;text-decoration:none}

  /* content */
  .section-title{font-family:"Mulish",Arial,sans-serif;font-weight:400;font-size:19.5px;color:var(--ink);letter-spacing:.2px}
  .welcome-title{left:110px;top:580px}
  .welcome-photo{left:110px;top:627px;width:99px;height:134px;
    background:linear-gradient(180deg,#6f9fd6 0%,#a7c8ea 45%,#5aa631 70%,#3c8a1f 100%)}
  .welcome-copy{left:226px;top:622px;width:270px;font-size:11.1px;line-height:15.6px;color:var(--body)}
  .welcome-copy p{margin-bottom:15.6px}
  .column-rule{left:521px;top:562px;width:1px;height:396px;background:var(--rule)}

  .results-title{left:552px;top:580px}
  .results-list{left:552px;top:621px;width:379px;list-style:none}
  .results-list li{position:relative;padding:0 0 7px 16px;margin-bottom:8px;border-bottom:1px solid var(--rule);
    font-size:11.1px;line-height:15.6px;color:var(--ink)}
  .results-list li:last-child{border-bottom:none}
  .results-list li svg{position:absolute;left:0;top:4px}
  .results-list li.is-highlight{color:var(--yellow)}
  .contact-line{left:549px;top:873px;width:390px;font-size:15.3px;line-height:19.2px;color:var(--ink)}
  .contact-line span{color:var(--green)}

  /* memberships */
  .memberships{left:0;top:1008px;width:1042px;height:122px;background:var(--green);text-align:center;color:var(--white)}
  .memberships h2{font-family:"Mulish",Arial,sans-serif;font-weight:400;font-size:19px;margin-top:28px}
  .memberships p{font-size:11px;line-height:15.8px;margin-top:4px}

  .footer{left:0;top:1147px;width:1042px;text-align:center}
  .footer .address{font-size:9.4px;color:var(--muted)}
  .footer .legal{font-size:7.6px;color:var(--ink);margin-top:5px}
</style>
</head>
<body>

<header class="site-header abs">
  <div class="brand abs"><span class="brand-square"></span>Tovimar Inc.</div>
  <nav class="main-nav abs">
    <a href="#">HOME</a>
    <a href="#">COMPANY</a>
    <a href="#">SERVICES</a>
    <a href="#" class="is-active">HOUSING REHAB APPLICATION</a>
    <a href="#">AFFORDABLE APPLICATION</a>
    <a href="#">CONTACT</a>
  </nav>
</header>

<div class="dropdown abs">
  <a href="#">LAKEWOOD</a>
  <a href="#">BRICK</a>
  <a href="#">JACKSON</a>
  <a href="#">WARREN</a>
</div>

<section class="hero abs" role="img" aria-label="Photo of a planning team meeting around a table with blueprints and yellow hard hats"></section>
<div class="hero-band abs"></div>
<ul class="hero-points abs">
  <li>Community Development Planning</li>
  <li>Housing Rehabilitation Administration</li>
  <li>US Department of Housing and Urban Development (HUD) Program Management</li>
  <li>Implementation of Programs under the Jurisdiction of New Jersey Council of Affordable Housing (COAH)</li>
</ul>
<a href="#" class="cta abs">CALL TO ACTION &nbsp;<svg width="7" height="10" viewBox="0 0 7 10"><path d="M1 1l4 4-4 4" fill="none" stroke="#3a3000" stroke-width="2"/></svg></a>

<h1 class="section-title welcome-title abs">WELCOME TO TOVIMAR</h1>
<div class="welcome-photo abs" role="img" aria-label="Photo of a surveyor with a tripod instrument in a green field"></div>
<div class="welcome-copy abs">
  <p>Tovimar, Inc. is a city planning firm that specializes in community development and housing rehabilitation program planning, design and implementation. We have over twenty years of experience in developing and administering income base-base housing and programs in accordance with US Department of Housing and Urban Development (HUD) and New Jersey Council on Affordable Housing (COAH) rules and regulations,</p>
  <p>In addition, our firm is capable of providing the technical and administrative assistance our clients require for implementation of their income based housing programs. Halvern Marsh Associates is one of the most experience urban planning firms in New Jersey, with over forty years of as consulting planners.</p>
  <p>To find out more about federal housing programs that we will administer, please go to www.housingprograms-info.org</p>
</div>
<div class="column-rule abs"></div>

<h2 class="section-title results-title abs">WE GET RESULTS</h2>
<ul class="results-list abs">
  <li><svg width="11" height="9" viewBox="0 0 11 9"><path d="M1 4.5l3 3 6-6" fill="none" stroke="#b5b5b5" stroke-width="2"/></svg>Tovimar designs income based programs to be supported by federal placement lotteries state funding.</li>
  <li><svg width="11" height="9" viewBox="0 0 11 9"><path d="M1 4.5l3 3 6-6" fill="none" stroke="#b5b5b5" stroke-width="2"/></svg>We implement local programs to benefit people seeking access to affordable housing.</li>
  <li><svg width="11" height="9" viewBox="0 0 11 9"><path d="M1 4.5l3 3 6-6" fill="none" stroke="#b5b5b5" stroke-width="2"/></svg>Our experienced staff screen applicants for local affordable housing.</li>
  <li><svg width="11" height="9" viewBox="0 0 11 9"><path d="M1 4.5l3 3 6-6" fill="none" stroke="#b5b5b5" stroke-width="2"/></svg>We pre-qualify persons who have applied for housing rehabilitation.</li>
  <li class="is-highlight"><svg width="11" height="9" viewBox="0 0 11 9"><path d="M1 4.5l3 3 6-6" fill="none" stroke="#f1c100" stroke-width="2"/></svg>Conduct placement lotteries</li>
  <li><svg width="11" height="9" viewBox="0 0 11 9"><path d="M1 4.5l3 3 6-6" fill="none" stroke="#b5b5b5" stroke-width="2"/></svg>Through local housing rehabilitation programs, our experience construction inspectors determine what improvements are required at eligible units based on local building codes and health and safety issues.</li>
</ul>
<p class="contact-line abs">For more information about out services,<br>please contact us today at <span>TOVIMAR (732) 555-0184<br>or info@tovimarplanning.com</span></p>

<section class="memberships abs">
  <h2>MEMBERSHIPS</h2>
  <p>National Neighborhood Renewal Council &nbsp;&nbsp; Garden State Planning Society<br>Coastal Planning Officials Forum Shoreline Community Development League</p>
</section>

<footer class="footer abs">
  <p class="address">Copy Right 2014 Tovimar, 218 Harbor Point Road, Brick, New Jersey, 08700 &nbsp;&nbsp; TEL (732) 555-0184 Fax (732) 555-0193</p>
  <p class="legal">©2014 - Terms</p>
</footer>

</body>
</html>
```